Redesign of business card for Cedar Ridge Mechanical

We are looking for a new design for our business cards for Cedar Ridge Mechanical. We are a plumbing & HVAC construction company, operating on the West Coast of Canada and USA. Logo attached.
Industry/Entity Type
Construction - Plumbing & HVAC
Contact Information for Business Card
Name, address, phone numbers, email, website address
Look and feel
Each slider illustrates characteristics of the customer's brand and the style your logo design should communicate.

```html
<!DOCTYPE html>
<html lang="en">
<head>
<meta charset="utf-8">
<title>Cedar Ridge Mechanical — Business Card</title>
<link href="https://fonts.googleapis.com/css2?family=Montserrat:wght@300;400;600;700&display=swap" rel="stylesheet">
<style>
  :root {
    --page: #111111;
    --card: #1b1b1b;
    --card-back: #1e1e1e;
    --band: #3f3f40;
    --ink: #ffffff;
    --muted: #8c8c8c;
  }
  * { box-sizing: border-box; margin: 0; padding: 0; }
  html, body { width: 1200px; height: 963px; overflow: hidden; background: var(--page); }
  .stage {
    width: 1200px; height: 963px;
    display: flex; align-items: center; justify-content: center; gap: 60px;
    font-family: "Montserrat", sans-serif;
  }
  .card {
    position: relative; width: 520px; height: 297px;
    border-radius: 18px; overflow: hidden;
    box-shadow: 0 18px 40px rgba(0,0,0,.55);
  }
  .card--front { background: var(--card); color: var(--ink); }
  .card--back { background: var(--card-back); }
  .card svg.frame { position: absolute; inset: 0; }
  .identity {
    position: absolute; right: 262px; top: 118px; text-align: right;
  }
  .identity__name { font-weight: 700; font-size: 20px; letter-spacing: .5px; text-transform: uppercase; }
  .identity__role { font-weight: 300; font-size: 14px; margin-top: 2px; }
  .divider {
    position: absolute; left: 270px; top: 112px; width: 1px; height: 84px; background: var(--ink);
  }
  .contacts { position: absolute; left: 284px; top: 120px; list-style: none; }
  .contacts li {
    display: flex; align-items: center; gap: 7px;
    font-size: 13px; font-weight: 400; line-height: 22px;
  }
  .contacts svg { width: 13px; height: 13px; flex: none; }
  .address {
    position: absolute; left: 90px; width: 330px; bottom: 9px;
    text-align: center; font-size: 12px; font-weight: 400;
  }
  .brand {
    position: absolute; inset: 0;
    display: flex; align-items: center; justify-content: center;
    font-weight: 600; font-size: 27px; letter-spacing: 1.5px;
    text-transform: uppercase; color: var(--muted);
  }
</style>
</head>
<body>
<main class="stage">
  <section class="card card--front" aria-label="Card front">
    <svg class="frame" viewBox="0 0 520 297" fill="none" stroke="var(--ink)" stroke-width="3" stroke-linecap="round">
      <path d="M16 60 V32 Q16 16 32 16 H78"/>
      <path d="M96 16 H488 Q504 16 504 32 V56"/>
      <path d="M504 74 V265 Q504 281 488 281 H430"/>
      <path d="M80 281 H32 Q16 281 16 265 V240"/>
    </svg>
    <div class="identity">
      <p class="identity__name">Daniel Brooks</p>
      <p class="identity__role">Manager</p>
    </div>
    <span class="divider"></span>
    <ul class="contacts">
      <li>
        <svg viewBox="0 0 16 16" fill="var(--ink)"><path d="M3 1.5 L6 1 L7.5 5 L5.6 6.4 Q7 9.6 9.6 10.4 L11 8.5 L15 10 L14.5 13 Q13.6 15 11 14.6 Q2.4 12.6 1.4 4.4 Q1.2 2 3 1.5Z"/></svg>
        123-456-2100
      </li>
      <li>
        <svg viewBox="0 0 16 16" fill="none" stroke="var(--ink)" stroke-width="1.6"><rect x="1.5" y="3.5" width="13" height="9" rx="1"/><path d="M2 4.5 L8 9 L14 4.5"/></svg>
        youremail@mailbox.com
      </li>
      <li>
        <svg viewBox="0 0 16 16" fill="none" stroke="var(--ink)" stroke-width="1.4"><circle cx="8" cy="8" r="6.5"/><ellipse cx="8" cy="8" rx="3" ry="6.5"/><path d="M1.5 8 H14.5"/></svg>
        www.yourwebsite.com
      </li>
    </ul>
    <p class="address">Your address, city, state, ZIP 0000</p>
  </section>

  <section class="card card--back" aria-label="Card back">
    <svg class="frame" viewBox="0 0 520 297" fill="none">
      <rect x="24" y="24" width="472" height="249" rx="30" stroke="var(--band)" stroke-width="18"/>
    </svg>
    <p class="brand">Cedar Ridge Mechanical</p>
  </section>
</main>
</body>
</html>
```